Meadow Paw Web Site

We have basically a start up business that I need help with. This project is just for the web site.

Our product is a frozen raw pet food that promotes weight control, less shedding, smaller stools and an overall better health. The product is in nugget form similar to what you would see in a steak shish kabob. I only share that with you in case you want to incorporate that in the design.

We have been in business for 17 years but all of our sales have been word of mouth. We are going to be launching an infomercial this summer and I need everything stated previously to be completed before we can launch the infomercial.

We need the following (6) pages:

Home:
This is where we need to have the ability to purchase our products. Our main goal is to get the consumer to purchase our product. We have our own shopping cart so we just need to allow for the insertion of that shopping cart.

Why Raw:
This will just be a page with 4-5 paragraphs and an embedded YouTube video.

How to Use:
We will need a page with a chart (4 Columns wide with 6 rows) as well as an embedded YouTube video.

Customer Success Stories:
Allow us to add these as we move forward. I need a placeholder for an image of the customers pet and a paragraph or two explaining the situation

Where to Buy:
- Online - Find a Retailer - Find a Local Distributor - Call to Order

Contact Us:
Copper Ridge Holdings, Inc.
2740 Copper Rd
Eagan, MN 55148
(800) xxx-xxxx

We need to provide links to our to be created... Facebook page, Twitter Account, Youtube Channel, Google circle, Blog
Updates

All, I have received many front page designs that look good.  Please notice in the brief that I need multiple pages built not just the home page.  

Thanks,

Dale

Reason: I need to see the rest of the pages. Thanks, Dale

Target Market(s)

Women between the ages of 30 & 60.

Industry/Entity Type

Shopping

```html
<!DOCTYPE html>
<html lang="en">
<head>
<meta charset="utf-8">
<title>Meadow Paw</title>
<link href="https://fonts.googleapis.com/css2?family=Arimo:wght@400;700&family=Open+Sans:ital,wght@0,600;0,700;1,600;1,700&display=swap" rel="stylesheet">
<style>
:root{
  --rust:#b8450f;
  --orange:#c9501a;
  --orange-light:#f6a21b;
  --accent:#c4420d;
  --dark:#474747;
  --darker:#3a3a3a;
  --panel:#4a4a4a;
  --line:#d8d8d8;
  --text:#666;
  --white:#fff;
}
*{margin:0;padding:0;box-sizing:border-box}
html,body{width:928px;height:1200px;overflow:hidden}
body{position:relative;background:var(--white);font-family:"Arimo",Arial,sans-serif;color:var(--text)}
.abs{position:absolute}
.topbar{left:0;top:0;width:928px;height:28px;background:var(--rust);color:var(--white);font-size:8px}
.topbar .site{position:absolute;left:134px;top:9px}
.topbar .links{position:absolute;left:435px;top:9px;display:flex;gap:0}
.topbar .links span{display:inline-block}
.topbar .sep{margin:0 22px}
.header{left:0;top:28px;width:928px;height:136px;background:linear-gradient(#d4641c,#e8861f 55%,#f5a21d)}
.logo{left:135px;top:64px;display:flex;align-items:center;gap:7px;color:var(--white);font-family:"Open Sans",sans-serif;font-weight:700;font-size:20px}
.logo .dot{width:18px;height:18px;border-radius:50%;background:#2a1a0d}
.tagline{left:303px;top:52px;color:var(--white);font-family:"Open Sans",sans-serif;font-style:italic;font-weight:600;font-size:19px;line-height:24px;letter-spacing:-.4px}
.search{left:631px;top:48px;width:163px;height:23px;background:var(--white);font-size:8px;color:#888;padding:8px 9px}
.search svg{position:absolute;right:7px;top:5px}
.call{left:610px;top:86px;color:var(--white);font-size:9px;display:flex;align-items:center;gap:5px}
.call b{font-size:13px;font-weight:700;margin-left:2px}
.nav{left:133px;top:129px;width:662px;height:35px;background:linear-gradient(#fafafa,#e6e6e6);border:1px solid #ccc;font-size:9px;color:#444}
.nav .item{position:absolute;top:13px}
.follow{background:var(--dark);display:flex;align-items:center;gap:6px;color:var(--white);font-size:9px;padding-left:12px}
.follow .lbl{margin-right:3px}
.follow i{display:block;width:21px;height:21px;border:1px solid #8a8a8a;background:#5a5a5a}
.nav .follow{position:absolute;right:-1px;top:-1px;width:194px;height:35px}
.h2{font-size:10.5px;color:var(--accent);text-transform:uppercase}
.cat{left:133px;width:163px;height:27px;border:1px solid var(--line);font-size:9px;color:#555;padding:8px 11px}
.cat svg{position:absolute;right:7px;top:8px}
.cat.active{background:var(--orange);border-color:var(--orange);color:var(--white)}
.banner{left:316px;top:180px;width:479px;height:227px;background:linear-gradient(90deg,#f3c5b3,#f8e4da 55%,#ead6c8);overflow:hidden}
.banner .photo{position:absolute;right:0;top:0;width:230px;height:227px;background:linear-gradient(#f6ebe3,#d8b9a4 70%,#cc8d6a)}
.banner .title{position:absolute;left:38px;top:44px;font-family:"Open Sans",sans-serif;font-style:italic;font-weight:700;font-size:32px;color:#cf5a1c;letter-spacing:-1.3px}
.banner .sub{position:absolute;left:38px;top:92px;font-family:"Open Sans",sans-serif;font-style:italic;font-weight:600;font-size:13.5px;line-height:15px;color:#3b3b3b;letter-spacing:-.3px}
.banner .body{position:absolute;left:38px;top:131px;width:210px;font-family:"Open Sans",sans-serif;font-size:7.5px;line-height:16.5px;color:#333}
.banner .arrows{position:absolute;right:9px;top:196px;display:flex;gap:1px}
.btn-arrow{width:20px;height:20px;background:var(--accent);display:flex;align-items:center;justify-content:center}
.mini-arrows{display:flex;gap:1px}
.mini-arrows span{width:10px;height:10px;background:var(--accent);display:flex;align-items:center;justify-content:center}
.stories{left:133px;top:449px;width:163px;height:209px;background:var(--panel);color:var(--white)}
.story{position:absolute;left:15px;width:140px}
.story h4{font-size:7.5px;font-weight:400}
.story .pic{position:absolute;left:0;top:14px;width:45px;height:42px}
.story p{position:absolute;left:56px;top:16px;width:80px;font-size:7px;font-style:italic;line-height:13px;color:#ddd}
.stories .divider{position:absolute;left:0;top:86px;width:163px;height:1px;background:#5e5e5e}
.stories .more{position:absolute;left:13px;top:172px;width:138px;height:24px;background:linear-gradient(#fff,#dcdcdc);color:#555;font-size:7.5px;text-align:center;padding-top:8px}
.card{width:150px;height:212px;border:1px solid var(--line);background:var(--white)}
.card .pic{position:absolute;left:18px;top:14px;width:112px;height:112px}
.card h5{position:absolute;left:18px;top:131px;font-size:8.5px;font-weight:400;color:var(--accent);white-space:nowrap}
.card p{position:absolute;left:18px;top:147px;width:120px;font-size:7.5px;line-height:13.5px;color:#888}
.card .price{position:absolute;left:18px;top:186px;font-size:12px;color:var(--accent)}
.buy{position:absolute;width:64px;height:20px;background:var(--orange);color:var(--white);font-size:7px;text-align:center;padding-top:6px}
.card .buy{left:77px;top:181px}
.special{left:133px;top:707px;width:163px;height:119px;border:1px solid var(--line)}
.footer{left:0;top:954px;width:928px;height:204px;background:var(--dark)}
.copyright{left:0;top:1158px;width:928px;height:42px;background:var(--darker);color:#ddd;font-size:7px;text-align:center;padding-top:17px}
.fcol{position:absolute;top:27px}
.fcol h6{font-size:9px;font-weight:400;color:var(--white);margin-bottom:10px}
.fcol a{display:block;font-size:7px;color:#bbb;text-decoration:none;height:16.6px}
.fcontact{color:#ccc;font-size:7px;line-height:16.6px}
.fcontact .callnow{color:var(--white);font-size:9px;margin-top:6px}
.fcontact .num{color:var(--white);font-size:13px;margin-top:4px}
.footer .follow{position:absolute;left:601px;top:143px;width:194px;height:34px;border:1px solid #5c5c5c;padding-left:12px}
</style>
</head>
<body>

<div class="abs topbar">
  <span class="site">www.meadowpaw.com</span>
  <div class="links">
    <span>Home</span><span class="sep">|</span><span>My Account</span><span class="sep">|</span><span>Login</span><span class="sep">|</span><span>Register</span>
    <span style="margin-left:18px;display:flex;align-items:center;gap:5px">
      <svg width="9" height="8" viewBox="0 0 9 8"><path d="M0 1h2l1 4h5l1-3H3" fill="none" stroke="#fff" stroke-width="1"/><circle cx="4" cy="7" r=".8" fill="#fff"/><circle cx="7" cy="7" r=".8" fill="#fff"/></svg>
      Your cart is : 0 Items</span>
  </div>
</div>

<div class="abs header"></div>
<div class="abs logo"><span class="dot"></span>Meadow Paw</div>
<div class="abs tagline">We are dog RAW food creator<br>and seller.</div>
<div class="abs search">Search :
  <svg width="12" height="12" viewBox="0 0 12 12"><circle cx="5" cy="5" r="3.8" fill="none" stroke="#999" stroke-width="1.3"/><path d="M8 8l3 3" stroke="#999" stroke-width="1.5"/></svg>
</div>
<div class="abs call">
  <svg width="13" height="13" viewBox="0 0 13 13"><path d="M2 1l3 0 1 3-2 1c1 2 2 3 4 4l1-2 3 1 0 3c-6 1-11-4-10-10z" fill="#fff"/></svg>
  CALL US NOW : <b>( 1408 ) 320 556</b>
</div>

<nav class="abs nav">
  <span class="item" style="left:21px">Home</span>
  <span class="item" style="left:77px">Why RAW</span>
  <span class="item" style="left:150px">How to Use</span>
  <span class="item" style="left:228px">Success Stories</span>
  <span class="item" style="left:323px">Where to Buy</span>
  <span class="item" style="left:409px">Contact us</span>
  <div class="follow"><span class="lbl">Follow Us :</span><i></i><i></i><i></i><i></i><i></i></div>
</nav>

<div class="abs h2" style="left:133px;top:181px">Categories</div>
<div class="abs cat active" style="top:201px">Raw Frozen Formulas<svg width="6" height="10" viewBox="0 0 6 10"><path d="M1 1l4 4-4 4" fill="none" stroke="#fff" stroke-width="1.2"/></svg></div>
<div class="abs cat" style="top:231px">Raw Pronto Formulas<svg width="6" height="10" viewBox="0 0 6 10"><path d="M1 1l4 4-4 4" fill="none" stroke="#999" stroke-width="1"/></svg></div>
<div class="abs cat" style="top:261px">Freeze-Dried Formulas<svg width="6" height="10" viewBox="0 0 6 10"><path d="M1 1l4 4-4 4" fill="none" stroke="#999" stroke-width="1"/></svg></div>
<div class="abs cat" style="top:291px">Raw Frozen Mixes<svg width="6" height="10" viewBox="0 0 6 10"><path d="M1 1l4 4-4 4" fill="none" stroke="#999" stroke-width="1"/></svg></div>
<div class="abs cat" style="top:320px">Raw Frozen Grinds<svg width="6" height="10" viewBox="0 0 6 10"><path d="M1 1l4 4-4 4" fill="none" stroke="#999" stroke-width="1"/></svg></div>
<div class="abs cat" style="top:350px">Raw Meaty Bones<svg width="6" height="10" viewBox="0 0 6 10"><path d="M1 1l4 4-4 4" fill="none" stroke="#999" stroke-width="1"/></svg></div>
<div class="abs cat" style="top:380px">Recreation Bones<svg width="6" height="10" viewBox="0 0 6 10"><path d="M1 1l4 4-4 4" fill="none" stroke="#999" stroke-width="1"/></svg></div>

<section class="abs banner">
  <div class="photo" role="img" aria-label="Photo of a dog in a checked bib at a table with sausages on a plate and a glass of milk"></div>
  <div class="title">Meadow Paw</div>
  <div class="sub">We are dog RAW food creator<br>and seller.</div>
  <div class="body">Lorem Ipsum is simply dummy text of the printing and typesetting industry. Lorem Ipsum has been the industry's standard dummy...</div>
  <div class="arrows">
    <span class="btn-arrow"><svg width="7" height="10" viewBox="0 0 7 10"><path d="M5 1L1 5l4 4" fill="none" stroke="#fff" stroke-width="1.3"/></svg></span>
    <span class="btn-arrow"><svg width="7" height="10" viewBox="0 0 7 10"><path d="M2 1l4 4-4 4" fill="none" stroke="#fff" stroke-width="1.3"/></svg></span>
  </div>
</section>

<div class="abs h2" style="left:133px;top:427px">Success Stories</div>
<section class="abs stories">
  <div class="story" style="top:16px">
    <h4>LOREM IPSUM IS SIMPLY DUMMY :</h4>
    <div class="pic" role="img" aria-label="Customer's dog photo" style="background:linear-gradient(135deg,#8a5a3a,#c9a17f)"></div>
    <p>Lorem Ipsum is simply dummy text of the printing...</p>
  </div>
  <div class="divider"></div>
  <div class="story" style="top:99px">
    <h4>LOREM IPSUM IS SIMPLY DUMMY :</h4>
    <div class="pic" role="img" aria-label="Customer's dog in a red sweater photo" style="background:linear-gradient(135deg,#e9e2d8,#c8352c)"></div>
    <p>Lorem Ipsum is simply dummy text of the printing...</p>
  </div>
  <div class="more">VIEW MORE STORIES &raquo;</div>
</section>

<div class="abs h2" style="left:316px;top:427px">New Products</div>
<div class="abs mini-arrows" style="left:772px;top:428px">
  <span><svg width="4" height="6" viewBox="0 0 4 6"><path d="M3 0L0 3l3 3" fill="none" stroke="#fff"/></svg></span>
  <span><svg width="4" height="6" viewBox="0 0 4 6"><path d="M1 0l3 3-3 3" fill="none" stroke="#fff"/></svg></span>
</div>

<div class="abs card" style="left:316px;top:452px">
  <div class="pic" role="img" aria-label="Rolls of raw frozen dog food with box" style="background:radial-gradient(circle,#e3c6a8,#fff 70%)"></div>
  <h5>Lorem Ipsum is simply dummy</h5><p>Lorem Ipsum is simply dummy text of the printing...</p><span class="price">$ 6.00</span><span class="buy">BUY NOW</span>
</div>
<div class="abs card" style="left:481px;top:452px">
  <div class="pic" role="img" aria-label="Bag of freeze-dried dog food" style="background:radial-gradient(circle,#8c7a4a,#fff 70%)"></div>
  <h5>Lorem Ipsum is simply dummy</h5><p>Lorem Ipsum is simply dummy text of the printing...</p><span class="price">$ 6.00</span><span class="buy">BUY NOW</span>
</div>
<div class="abs card" style="left:645px;top:452px">
  <div class="pic" role="img" aria-label="Clear resealable pouch of dog treats" style="background:radial-gradient(circle,#8fbf8a,#fff 70%)"></div>
  <h5>Lorem Ipsum is simply dummy</h5><p>Lorem Ipsum is simply dummy text of the printing...</p><span class="price">$ 6.00</span><span class="buy">BUY NOW</span>
</div>

<div class="abs h2" style="left:133px;top:682px">Special Products</div>
<div class="abs mini-arrows" style="left:270px;top:682px">
  <span><svg width="4" height="6" viewBox="0 0 4 6"><path d="M3 0L0 3l3 3" fill="none" stroke="#fff"/></svg></span>
  <span><svg width="4" height="6" viewBox="0 0 4 6"><path d="M1 0l3 3-3 3" fill="none" stroke="#fff"/></svg></span>
</div>
<div class="abs special">
  <div role="img" aria-label="Row of red dog food bags" style="position:absolute;left:8px;top:16px;width:145px;height:88px;background:radial-gradient(ellipse,#d83a2e,#fff 72%)"></div>
</div>
<div class="abs" style="left:133px;top:837px;font-size:10.5px;color:var(--accent)">Lorem Ipsum is simply dummy</div>
<div class="abs" style="left:133px;top:857px;width:160px;font-size:7.5px;line-height:16px;color:#888">Lorem Ipsum is simply dummy text of the psum is simply is simply dummy...</div>
<div class="abs" style="left:133px;top:903px;font-size:12px;color:var(--accent)">$ 6.00</div>
<span class="buy" style="left:232px;top:898px">BUY NOW</span>

<div class="abs h2" style="left:316px;top:682px">Featured Products</div>
<div class="abs mini-arrows" style="left:772px;top:682px">
  <span><svg width="4" height="6" viewBox="0 0 4 6"><path d="M3 0L0 3l3 3" fill="none" stroke="#fff"/></svg></span>
  <span><svg width="4" height="6" viewBox="0 0 4 6"><path d="M1 0l3 3-3 3" fill="none" stroke="#fff"/></svg></span>
</div>

<div class="abs card" style="left:316px;top:707px">
  <div class="pic" role="img" aria-label="Green box of dog food" style="left:26px;width:104px;background:linear-gradient(135deg,#a8b86a,#6c8a3a)"></div>
  <h5>Lorem Ipsum is simply dummy</h5><p>Lorem Ipsum is simply dummy text of the printing...</p><span class="price">$ 6.00</span><span class="buy">BUY NOW</span>
</div>
<div class="abs card" style="left:481px;top:707px">
  <div class="pic" role="img" aria-label="Bag of frozen chicken formula dog food" style="background:linear-gradient(#f4efe4,#e9d9b8 60%,#c9737a)"></div>
  <h5>Lorem Ipsum is simply dummy</h5><p>Lorem Ipsum is simply dummy text of the printing...</p><span class="price">$ 6.00</span><span class="buy">BUY NOW</span>
</div>
<div class="abs card" style="left:645px;top:707px">
  <div class="pic" role="img" aria-label="Dark red bag of raw dog food nuggets" style="left:34px;width:82px;background:linear-gradient(#5a1a14,#7a2a20 50%,#c9b08a)"></div>
  <h5>Lorem Ipsum is simply dummy</h5><p>Lorem Ipsum is simply dummy text of the printing...</p><span class="price">$ 6.00</span><span class="buy">BUY NOW</span>
</div>

<footer class="abs footer">
  <div class="fcol" style="left:133px"><h6>CATEGORIES</h6>
    <a>Raw Frozen Formulas</a><a>Raw Pronto Formulas</a><a>Freeze-Dried Formulas</a><a>Raw Frozen Mixes</a><a>Raw Frozen Grinds</a><a>Raw Meaty Bones</a><a>Recreation Bones</a><a>Treats</a><a>All Products</a></div>
  <div class="fcol" style="left:270px"><h6>INFORMATION</h6>
    <a>About Us</a><a>Customer Service</a><a>Privacy Policy</a><a>Site Map</a><a>Search Terms</a><a>Advanced Search</a><a>Orders and Returns</a><a>Contact Us</a></div>
  <div class="fcol" style="left:403px"><h6>WHY BUY FROM US</h6>
    <a>About Us</a><a>Customer Service</a><a>Privacy Policy</a><a>Site Map</a><a>Search Terms</a><a>Advanced Search</a><a>Orders and Returns</a><a>Contact Us</a></div>
  <div class="fcol" style="left:549px"><h6>MY ACCOUNT</h6>
    <a>Sign In</a><a>View Cart</a><a>My Wishlist</a><a>Track My Order</a><a>Help</a></div>
  <div class="fcol fcontact" style="left:675px"><h6>CONTACTS</h6>
    <div>120 Street name, State name,<br>Country name, Zip code : 210 1102</div>
    <div class="callnow">CALL US NOW :</div>
    <div class="num">( 1408 ) 320 556</div></div>
  <div class="follow"><span class="lbl">Follow Us :</span><i></i><i></i><i></i><i></i><i></i></div>
</footer>
<div class="abs copyright">Copyrights &copy; 2014. Meadow Paw. All Rights Reserved</div>

</body>
</html>
```